Eco-friendly waste company needs flyer design to promote collections

We need a flyer to promote our new small item collection service, offering cheaper waste collections to customers who usually would not want to pay for our high-eco performance business (we are expensive compared to companies who dispose of their waste in less eco-friendly ways). This flyer needs to be professional, informational, and classy to appeal to corporate office-based customers. We want photos used where possible, not cartoon or illustrations of objects we collect. I will attach our logo in various designs, and am really open to design options. We have a website that is ourdated, uses cartoons etc, and this is not landing well with our customer base so we want to move away from that kind of design. I need an A5-sized flyer, double sided. Please ask me if you have any questions!
Hi all,
Thank you all so much for so many wonderful designs, I will be looking through all of these tomorrow with my CEO and then I will update the project status again.
Thanks!!
Kind regards,
Nora

Hi all,
Thanks!!
Kind regards,
Nora

```html
<!DOCTYPE html>
<html lang="en">
<head>
<meta charset="utf-8">
<title>Verda Cycle – Small Item Collection Flyer</title>
<link href="https://fonts.googleapis.com/css2?family=Arimo:wght@400;700&display=swap" rel="stylesheet">
<style>
  :root {
    --green: #43b08e;
    --recycle: #1f9a48;
    --ink: #111111;
    --text: #1d1d1d;
    --paper: #ffffff;
    --backdrop: #d3d3d3;
    --photo-dark: #3b4756;
    --photo-mid: #8a8f96;
  }
  * { margin: 0; padding: 0; box-sizing: border-box; }
  html, body { width: 1200px; height: 1200px; overflow: hidden; }
  body { background: var(--backdrop); font-family: "Arimo", Arial, sans-serif; color: var(--text); position: relative; }

  .flyer { position: absolute; width: 460px; height: 652px; background: var(--paper); overflow: hidden; }
  .flyer--front { left: 104px; top: 230px; }
  .flyer--back { left: 658px; top: 234px; height: 650px; width: 458px; }
  .abs { position: absolute; }

  /* ---------- front ---------- */
  .brand { left: 18px; top: 19px; display: flex; align-items: center; gap: 10px; }
  .brand__dot { width: 48px; height: 48px; border-radius: 50%; border: 3px solid var(--green); }
  .brand__name { font-weight: 700; font-size: 23px; line-height: 24px; color: #2b2b2b; letter-spacing: .5px; }
  .brand__tagline { left: 28px; top: 76px; font-size: 7px; font-weight: 700; color: var(--green); letter-spacing: .3px; }

  .location-band { left: 0; top: 103px; width: 290px; height: 31px; background: var(--green); color: #fff;
    font-weight: 700; font-size: 11.5px; padding-left: 18px; line-height: 31px; }
  .hero-art { left: 0; top: 0; width: 460px; height: 230px; }
  .intro { left: 17px; top: 141px; width: 260px; font-size: 10.5px; line-height: 16px; }

  .items-tab { left: 0; top: 189px; width: 165px; height: 20px; background: var(--ink); color: #fff;
    font-weight: 700; font-size: 11px; line-height: 20px; padding-left: 18px;
    clip-path: polygon(0 0, 100% 0, 94% 100%, 0 100%); }
  .items-frame { left: 0; top: 200px; width: 343px; height: 245px; border-top: 1.5px solid var(--ink);
    border-right: 1.5px solid var(--ink); border-bottom: 1.5px solid var(--ink); }
  .green-panel { left: 351px; top: 201px; width: 109px; height: 247px; background: var(--green); }

  .item-list { left: 19px; top: 218px; list-style: none; font-size: 11px; line-height: 16.5px; }
  .item-list li { position: relative; padding-left: 10px; }
  .item-list li::before, .bullets li::before { content: ""; position: absolute; left: 0; top: 5px; width: 5px; height: 5px;
    border-radius: 50%; background: var(--green); }

  .photo-circle { width: 106px; height: 106px; border-radius: 50%; border: 3px solid #fff; box-shadow: 0 0 0 2px var(--green); }
  .photo-circle--parts { left: 298px; top: 214px; background: radial-gradient(circle at 45% 45%, #c9c4bd, #4d4b52 70%, #2a2a30); }
  .photo-circle--pile { left: 298px; top: 329px; background: linear-gradient(180deg, #9fb393 0%, #b7b7c0 45%, #6e6a74 70%, #6f9a4f 100%); }
  .recycle-art { border-radius: 8px; background: radial-gradient(circle, #47b36a, var(--recycle) 70%); opacity: .9; }
  .recycle-art--front { left: 196px; top: 229px; width: 80px; height: 80px; }

  .challenge { left: 53px; top: 445px; width: 347px; height: 46px; background: var(--ink); color: #fff;
    font-weight: 700; font-size: 10.5px; line-height: 14.5px; text-align: center; padding-top: 8px; }

  .conditions-bar { left: 19px; top: 508px; width: 53px; height: 124px; background: var(--green); }
  .conditions-bar span { position: absolute; left: 50%; top: 50%; transform: translate(-50%, -50%) rotate(-90deg);
    white-space: nowrap; color: #fff; font-weight: 700; font-size: 10.5px; line-height: 12px; text-align: center; }
  .conditions-box { left: 72px; top: 508px; width: 177px; height: 124px; border-top: 1.5px dashed var(--green);
    border-right: 1.5px dashed var(--green); text-align: center; }
  .vat { margin-top: 12px; font-weight: 700; font-size: 12px; line-height: 15px; }
  .postcode-tag { display: inline-block; margin-top: 8px; background: var(--green); color: #fff; font-weight: 700;
    font-size: 10.5px; padding: 3px 9px; }
  .postcodes { margin-top: 5px; font-size: 10.5px; line-height: 13px; padding: 0 6px; }

  .contact { left: 250px; top: 511px; width: 200px; text-align: center; font-size: 10.5px; line-height: 13px; }
  .contact__icon { display: block; margin: 8px auto 4px; }
  .contact__email { font-size: 9.5px; }
  .contact__phone { font-weight: 700; font-size: 12.5px; margin-top: 4px; }
  .front-foot { left: 0; top: 632px; width: 460px; height: 22px; background: var(--green); }

  /* ---------- back ---------- */
  .top-art { left: 0; top: 0; width: 458px; height: 200px; }
  .headline { left: 0; top: 150px; width: 458px; text-align: center; color: var(--green); font-weight: 700;
    font-size: 17px; line-height: 21px; }
  .subhead { left: 0; top: 196px; width: 458px; text-align: center; font-size: 12px; }
  .bullets { list-style: none; font-size: 10.5px; line-height: 11px; }
  .bullets li { position: relative; padding-left: 13px; margin-bottom: 5.5px; }
  .bullets li::before { top: 3px; width: 6px; height: 6px; }
  .price { color: var(--green); font-weight: 700; }
  .hazard-left { left: 19px; top: 229px; width: 205px; }
  .hazard-right { left: 238px; top: 225px; width: 200px; }
  .hazard-divider { left: 227px; top: 226px; width: 1px; height: 91px; background: #555; }

  .data-box { left: 63px; top: 333px; width: 330px; height: 51px; background: var(--ink); color: #fff;
    text-align: center; font-weight: 700; font-size: 16px; line-height: 20px; padding-top: 5px; }
  .data-copy { left: 25px; top: 394px; width: 415px; font-size: 10px; line-height: 16px; }
  .include-title { left: 27px; top: 433px; color: var(--green); font-weight: 700; font-size: 16px; }
  .include-left { left: 31px; top: 462px; }
  .include-right { left: 122px; top: 462px; }
  .include-left li, .include-right li { margin-bottom: 5px; font-size: 10.5px; }
  .include-divider { left: 110px; top: 459px; width: 1px; height: 92px; background: #555; }
  .recycle-art--back { left: 302px; top: 445px; width: 92px; height: 92px; }
  .certify { left: 0; top: 559px; width: 458px; text-align: center; font-size: 10px; line-height: 14px; padding: 0 15px; }
  .back-foot { left: 0; top: 597px; width: 458px; height: 53px; background: var(--green); color: #fff;
    text-align: center; font-weight: 700; font-size: 12px; line-height: 15px; padding-top: 12px; }
</style>
</head>
<body>

<section class="flyer flyer--front">
  <svg class="abs hero-art" viewBox="0 0 460 230">
    <defs>
      <linearGradient id="techGrad" x1="0" y1="0" x2="0" y2="1">
        <stop offset="0" stop-color="#f4f4f2"/>
        <stop offset=".5" stop-color="#d9d6cc"/>
        <stop offset="1" stop-color="#f2f2f0"/>
      </linearGradient>
    </defs>
    <circle cx="370" cy="86" r="92" fill="#ffffff"/>
    <g role="img" aria-label="Photo of old computers, monitors and office electronics">
      <circle cx="370" cy="86" r="90" fill="url(#techGrad)"/>
    </g>
    <circle cx="370" cy="86" r="93" fill="none" stroke="#111" stroke-width="1.5"/>
    <path d="M 360 -20 A 106 106 0 0 0 362 192" fill="none" stroke="var(--green)" stroke-width="9"/>
    <path d="M 462 128 A 106 106 0 0 1 402 186" fill="none" stroke="var(--green)" stroke-width="6"/>
    <polyline points="410,170 398,186 412,198" fill="none" stroke="var(--green)" stroke-width="6" stroke-linecap="round"/>
  </svg>

  <div class="abs brand">
    <span class="brand__dot"></span>
    <span class="brand__name">VERDA<br>CYCLE</span>
  </div>
  <p class="abs brand__tagline">SMALL LOADS, SMARTER DISPOSAL</p>

  <div class="abs location-band">ARE YOU LOCATED IN CENTRAL LONDON?</div>
  <p class="abs intro">Verda Cycle has the solution for you. We can collect items for £25 each on Wednesdays.</p>

  <div class="abs green-panel"></div>
  <div class="abs items-frame"></div>
  <div class="abs items-tab">EXAMPLE ITEMS ARE:</div>

  <ul class="abs item-list">
    <li>Printers</li>
    <li>Office furniture</li>
    <li>Whiteboards</li>
    <li>Shredders</li>
    <li>PC or television monitors</li>
    <li>Fans</li>
    <li>Plants and planter boxes</li>
    <li>Books and magazines (max 25kg)</li>
    <li>Pallet</li>
    <li>Packaging (cardboard boxes, polystyrene, plastic etc.)</li>
    <li>Paints and chemicals (max 7 litres)</li>
    <li>Light bulbs and fluorescent tubes (max 10 pieces)</li>
  </ul>

  <div class="abs recycle-art recycle-art--front" role="img" aria-label="Green recycling symbol graphic"></div>
  <div class="abs photo-circle photo-circle--parts" role="img" aria-label="Photo of computer parts and a keyboard"></div>
  <div class="abs photo-circle photo-circle--pile" role="img" aria-label="Photo of household items piled on a lawn for collection"></div>

  <div class="abs challenge">WE CAN TAKE MOST THINGS YOU CAN’T PUT IN YOUR<br>NORMAL BINS – CHALLENGE US!</div>

  <div class="abs conditions-bar"><span>CONDITIONS OF<br>OFFER:</span></div>
  <div class="abs conditions-box">
    <p class="vat">PRICE IS EXCLUSIVE<br>OF VAT</p>
    <span class="postcode-tag">ELIGIBLE POSTCODES:</span>
    <p class="postcodes">EC1, EC2, EC3, EC4, WC1,<br>WC2, W1, SW1, SE1, E1, E2,<br>N1, NW1</p>
  </div>

  <div class="abs contact">
    <p>If you have any questions please<br>email us at</p>
    <svg class="contact__icon" width="20" height="12" viewBox="0 0 20 12">
      <rect x="0.5" y="0.5" width="19" height="11" fill="var(--green)"/>
      <polyline points="1,1 10,7 19,1" fill="none" stroke="#fff" stroke-width="1.2"/>
    </svg>
    <p class="contact__email">bookings@verdacyclecollect.com</p>
    <svg class="contact__icon" width="16" height="16" viewBox="0 0 16 16">
      <rect width="16" height="16" rx="3" fill="var(--green)"/>
      <path d="M5 3.5 C4 4.5 4 8 6.5 10.8 C9 13.3 11.3 12.5 12 11.6 L10.5 10 L9.2 10.8 C8 10.2 6.5 8.6 6 7.3 L6.8 6 Z" fill="#fff"/>
    </svg>
    <p class="contact__phone">020 7946 0381</p>
  </div>

  <div class="abs front-foot"></div>
</section>

<section class="flyer flyer--back">
  <svg class="abs top-art" viewBox="0 0 458 200">
    <defs>
      <linearGradient id="cansGrad" x1="0" y1="0" x2="1" y2="1">
        <stop offset="0" stop-color="#5a6675"/>
        <stop offset=".4" stop-color="var(--photo-mid)"/>
        <stop offset=".7" stop-color="var(--photo-dark)"/>
        <stop offset="1" stop-color="#9a9aa0"/>
      </linearGradient>
    </defs>
    <rect width="458" height="165" fill="url(#cansGrad)" role="img" aria-label="Photo of discarded aerosol and paint cans"/>
    <path d="M0,160 Q228,55 458,150 L458,162 Q228,80 0,168 Z" fill="var(--green)"/>
    <path d="M0,168 Q228,80 458,162 L458,200 L0,200 Z" fill="#fff"/>
  </svg>

  <h1 class="abs headline">NEED TO GET RID OF ITEMS WHICH<br>CAN’T GO IN YOUR NORMAL BIN?</h1>
  <p class="abs subhead">We collect the following hazardous items:</p>

  <ul class="abs bullets hazard-left">
    <li>Paint - <span class="price">£4</span> per litre</li>
    <li>Fluorescent tubes and bulbs - <span class="price">£4</span> each</li>
    <li>Cooking oil / hydraulic oil / hazardous liquids–from <span class="price">£5</span> per litre</li>
    <li>TV / Computer monitors - <span class="price">£10</span> each</li>
  </ul>
  <div class="abs hazard-divider"></div>
  <ul class="abs bullets hazard-right">
    <li>Batteries – from <span class="price">£5</span> per kilo (depends on type)</li>
    <li>Gas bottles &amp; fire extinguishers - <span class="price">£35</span> each. Fridges – <span class="price">£40</span> for a small fridge, £125 for a commercial fridge, £200 for an ammonia fridge each</li>
    <li>Air conditioners - <span class="price">£30</span> each</li>
  </ul>

  <h2 class="abs data-box">NEED TO SECURELY DESTROY DATA<br>ON YOUR COMPUTER OR SERVER?</h2>
  <p class="abs data-copy">We can securely collect and wipe your data-holding electrical items, allowing for their safe reuse. Items that fail the wiping process will be securely shredded and recycled.</p>

  <h3 class="abs include-title">ITEMS INCLUDE:</h3>
  <ul class="abs bullets include-left">
    <li>Computers</li>
    <li>Laptops</li>
    <li>Servers</li>
    <li>Routers</li>
    <li>Switches</li>
  </ul>
  <div class="abs include-divider"></div>
  <ul class="abs bullets include-right">
    <li>Mobile phones</li>
    <li>Landline phones</li>
    <li>Printers with memory</li>
    <li>Photocopiers with memory</li>
  </ul>
  <div class="abs recycle-art recycle-art--back" role="img" aria-label="Green recycling symbol graphic"></div>

  <p class="abs certify">We can provide certificates confirming data secure destruction, either through securing wiping and reuse, or through shredding and recycling.</p>

  <div class="abs back-foot">We can also securely destroy any paper, files, documents<br>etc with our shredding service</div>
</section>

</body>
</html>
```